!! Innovative new tea company needs packaging design !!

** NB. We need this project as a starting point for our company. We would like to/ intend to have an ongoing relationship with the designer to add to/ change and develop the design in the future on freelance basis pending available workload.

We are in the process of creating a range of functional wellness drinks based on green tea - company name q~. We will have a range of drinks based on green tea attributed to functional effects - Zest, detox, Shield etc. Aim of the company is to create a healthy, modern, vibrant company that offers a range of drinks that offer healthy wellness properties, in great tasting fruit flavours.

We need packaging design for the boxes, initially for tea bags. dimensions will be Length – 12cm, Width – 6.75cm, Height – 7.75cm ( please note this means that the box will be TALL / UPRIGHT STANDING)

The brand name is q~ ( to represent green tea + other ingredients / effects). Four initial tea's will be produced that we need to show packaging for :

q~ Zest ( rasberry & pomegranite flavour )
q~ Shield ( orange & blueberry )
q~ detox ( apple & blackcurrant )
q~ multi vitamin ( lemon & peach )

We have had the below central brand logo and individual tea logo edits produced already, attached below.

*****Please note we intend the 4 packages to be the same consistent design - only change is on the title of each. For that reason we ONLY REQUEST TO SEE ONE DESIGN ON ONE PRODUCT from a designer to agree on format. Once agreed we will then request you give us the other 3 on agreed format ******

We are aiming to be a very young, vibrant company aiming at the 20 - 40 health conscious consumer. Were taking inspiration from companies like Pellucid smoothies and leaf owls and want branding to be in line with those themes.PLEASE LOOK THIS UP TO UNDERSTAND. We need box designs to be completed. Ideally building on the below designs weve had commissioned. However, if a better suggestion on the logo , or a tweak to these will improve the design then we are very much open to it.

Packaging must be, clear white background and bold colors along the line of each flavour teas colour ( ie red for Zest, yellow multi vitamin etc). We would ideally like the top and one side ( ONLY ) of the box to be coloured background ( matching the drink colour ). We are wanting simple and clear design FAIRLY MINIMALIST to convey the point of the brand to be simple clear and healthy ingredients. At the same time it must clearly stand out on a shelf. Lighthearted and not too serious, ideally simple, fun illustrated drawings ( ideally outlines/very simple drawings) of the fruit aligned to each flavour and any other branding / mascot logo design that you can suggest.

Also possible cartoon/simple illustration tea leaf somewhere on the box.

We need packaging for the 4 teas - 1 consistent design and theme, with only changes to color and a few illustrations per box.

Please note - We want text font to be funky, friendly, soft - various sizes on the text on the boxes - NOT everything the same size and generic font.

text to go on the box

( front of box):

- main Zest/Shield etc logo
.(tagline underneath) Wellness drinks

- * Green tea with vitamins drink

- * Natural Ceylon green tea with added vitamins and herbs to give you the best start to your day.

- * 5 reasons to drink this!!
100% natural ingredients
x% of your RDA of x
x mg of antioxidants to keep your heart healthy.
Naturally sweet taste
only x calories per cup!

(side of box)

Ingredients

We use only the finest hand picked ceylon green tea and mix it with natural fruit pieces, a hint of natural flavouring as our base. We add the goodness of burdock root and echinacea to help build your body's defenses and sweeten it with a dash of the south american stevia leaf to give a great tasting drink that will do you some good!

( side of box )

Nutrition Facts

Serving Size: 1 tea bag (4g)

Makes: 8 fl. oz.

Servings Per Container: 25

Amount Per Serving
Calories 0

% Daily Value*
Total Fat 0g
0%
Sodium 0mg
5%
Total Carb. 0g
0%
Sugars 10g
Protein 0g

* Percent Daily Values are based on a 2,000 calorie diet.

The above is how we forsee the packaging for now. However - anything that you can reccommend that is innovative to help us stand out to a young , trendy audience will be welcome.

Please message with any questions or comments.
Updates

Dear All - Please note - we have updated the brief with the packaging die line for your reference. Please note the box will be upstanding so designs should accomodate for a tall box.

Dear All - To reiterate key points of the brief - We request the deign to be stand out here. Majority white background with splashes/swirls/blotches of colour ( whatever design suggested ).Further to that, illustrations ( drawings - not pictures ) of fruit / tea leaves to stay in line with young, funky image. 

Overall theme is young, bright and modern - we need the packaging to reflect this. Not just standard text font and background colouring.
Any more clarity needed please contact us. 

Reason: Dear All We have increased the budget for this project and extended the deadline by additional 7 days. To date we have not received the designs we are happy with so want to give all added time to revise - follow the brief - and resubmit. Due to quality of designs received so far - we will not guarantee payment yet - HOWEVER - Intention is to get this completed for the business by next week latest- for that reason, as soon as someone has submitted a design that is at least along the right lines - we will then move to guarantee payment. Please also note - we intend to / hope to work with the designer directly on ongoing projects for the company so want a good - long term relationship from this. Good luck and please contact us if any more information needed. Regards

Dear all

Please can we request that for the sides of the box with a white background - text is in a green colour ( same shade as the original q~ logo green ). We would like this to be our standard font colour against white background. 

Obviously, please add colour where you see fit but we want a clean , consistent font across the boxes and eventually our web site. 

For the coloured backgrounds of the side and top - will leave up to you whatever colour font looks best. 

Reason: Deadline extended to provide some more feedback to designers. No decision yet made.

Target Market(s)

Young, health conscious individuals.

Industry/Entity Type

It Company

```html
<!DOCTYPE html>
<html lang="en">
<head>
<meta charset="utf-8">
<title>Tea box dielines</title>
<link href="https://fonts.googleapis.com/css2?family=Fredoka:wght@400;600&family=Quicksand:wght@500;700&display=swap" rel="stylesheet">
<style>
  :root {
    --orange: #ee5a2f;
    --pink: #d92d5a;
    --leaf: #8cbb4c;
    --leaf-light: #a9cd74;
    --white: #ffffff;
    --line: #8a8a8a;
    --page: #ffffff;
  }
  html, body { margin: 0; padding: 0; width: 1200px; height: 1191px; overflow: hidden; background: var(--page); }
  .dielines { display: block; width: 1200px; height: 1191px; }
  .box-shield { --accent: var(--orange); }
  .box-zest { --accent: var(--pink); }
  .cut { fill: var(--white); stroke: var(--line); stroke-width: 0.7; }
  .panel-white { fill: var(--white); stroke: var(--line); stroke-width: 0.7; }
  .panel-accent { fill: var(--accent); }
  .panel-leaf { fill: var(--leaf); }
  .flap-leaf { fill: var(--leaf-light); stroke: var(--line); stroke-width: 0.5; }
  .wordmark { font-family: "Quicksand", sans-serif; font-weight: 700; fill: var(--accent); }
  .wordmark-dot { fill: var(--leaf); }
  .heading { font-family: "Fredoka", sans-serif; font-weight: 600; }
  .body { font-family: "Quicksand", sans-serif; font-weight: 700; }
  .on-accent { fill: var(--white); }
  .t-accent { fill: var(--accent); }
  .t-leaf { fill: var(--leaf); }
  .facts-box { fill: var(--leaf); }
  .fruit-art { fill: url(#fruitTone); }
  .box-zest .fruit-art { fill: url(#fruitToneZest); }
</style>
</head>
<body>
<svg class="dielines" viewBox="0 0 1055 1047" xmlns="http://www.w3.org/2000/svg">
  <defs>
    <linearGradient id="fruitTone" x1="0" x2="1">
      <stop offset="0" stop-color="#ee5a2f"/><stop offset="0.7" stop-color="#e2672c"/><stop offset="1" stop-color="#4a3a7a"/>
    </linearGradient>
    <linearGradient id="fruitToneZest" x1="0" x2="1">
      <stop offset="0" stop-color="#c8284f"/><stop offset="0.7" stop-color="#d92d5a"/><stop offset="1" stop-color="#e04868"/>
    </linearGradient>
  </defs>

  <!-- Shield box -->
  <g class="box-shield">
    <path class="cut" d="M529 66 L518 66 L514 30 L500 20 L486 50 L486 140 L500 180 L529 195 Z"/>
    <path class="cut" d="M766 66 L777 66 L781 30 L795 20 L810 50 L810 140 L795 180 L766 195 Z"/>
    <path class="cut" d="M400 195 L405 170 L520 170 L529 195 Z"/>
    <path class="cut" d="M178 195 L186 177 L380 177 L390 195 Z"/>
    <path class="cut" d="M766 195 L775 168 L880 168 L891 195 Z"/>
    <path class="cut" d="M400 346 L405 370 L520 370 L529 346 Z"/>
    <path class="cut" d="M766 346 L775 372 L880 372 L891 346 Z"/>
    <path class="cut" d="M178 202 L137 210 L137 340 L178 346 Z"/>

    <rect class="panel-accent" x="529" y="18" width="237" height="48"/>
    <rect class="panel-white" x="529" y="66" width="237" height="129"/>
    <g transform="rotate(180 647 128)">
      <circle class="wordmark-dot" cx="602" cy="128" r="13"/>
      <text class="wordmark" x="622" y="137" font-size="25">Shield</text>
      <rect class="fruit-art" role="img" aria-label="Orange and blackberry illustration" x="730" y="112" width="50" height="30" rx="15"/>
    </g>

    <rect class="panel-white" x="178" y="195" width="222" height="151"/>
    <circle class="wordmark-dot" cx="200" cy="236" r="12"/>
    <text class="wordmark" x="218" y="244" font-size="22">Shield</text>
    <rect class="fruit-art" role="img" aria-label="Orange and blackberry illustration" x="334" y="218" width="48" height="28" rx="14"/>
    <text class="heading t-leaf" x="290" y="272" font-size="8.5" text-anchor="middle">5 reasons to drink this!!</text>
    <g class="body t-accent" font-size="5.6">
      <text x="203" y="292"><tspan class="t-leaf">+ </tspan>100% natural ingredients</text>
      <text x="203" y="300"><tspan class="t-leaf">+ </tspan>x% of your RDA of x</text>
      <text x="203" y="308"><tspan class="t-leaf">+ </tspan>x mg of antioxidants to keep your heart healthy.</text>
      <text x="203" y="316"><tspan class="t-leaf">+ </tspan>Naturally sweet taste</text>
      <text x="203" y="324"><tspan class="t-leaf">+ </tspan>only x calories per cup!</text>
    </g>

    <rect class="panel-accent" x="400" y="195" width="129" height="151"/>
    <text class="heading t-leaf" x="410" y="234" font-size="9.5">Nutrition Facts</text>
    <g class="body on-accent" font-size="5.2">
      <text x="410" y="242">Serving size: 1 tea bag (4g)</text>
      <text x="410" y="249">Makes: 8 fl. oz.</text>
      <text x="410" y="256">Servings per Container: 25</text>
    </g>
    <rect class="facts-box" x="405" y="262" width="114" height="58"/>
    <g class="body on-accent" font-size="5">
      <text x="409" y="270" font-size="6">Amount Per Serving</text>
      <text x="409" y="278">Calories</text><text x="445" y="278">0</text><text x="468" y="278">% Daily Value*</text>
      <text x="409" y="285">Total Fat</text><text x="445" y="285">0g</text><text x="468" y="285">0%</text>
      <text x="409" y="292">Sodium</text><text x="445" y="292">0mg</text><text x="468" y="292">5%</text>
      <text x="409" y="299">Total Carb.</text><text x="445" y="299">0g</text><text x="468" y="299">0%</text>
      <text x="409" y="306">Sugars</text><text x="445" y="306">10g</text>
      <text x="409" y="313">Protein</text><text x="445" y="313">0g</text>
      <text x="409" y="330">Percent Daily Values are based</text>
      <text x="409" y="337">on a 2,000 calorie diet</text>
    </g>

    <rect class="panel-white" x="529" y="195" width="237" height="151"/>
    <circle class="wordmark-dot" cx="594" cy="226" r="14"/>
    <text class="wordmark" x="615" y="236" font-size="27">Shield</text>
    <text class="body t-accent" x="660" y="246" font-size="5" text-anchor="middle">Green tea with vitamins drink</text>
    <rect class="fruit-art" role="img" aria-label="Orange and blackberry illustration" x="620" y="266" width="56" height="34" rx="17"/>
    <text class="heading t-accent" x="647" y="316" font-size="8.5" text-anchor="middle">orange &amp; blackberry flavour</text>
    <g class="body t-accent" font-size="4.8" text-anchor="middle">
      <text x="647" y="324">Natural Ceylon green tea with added vitamins and herbs to</text>
      <text x="647" y="330">give you the best start to your day</text>
    </g>

    <rect class="panel-accent" x="766" y="195" width="125" height="151"/>
    <text class="heading t-leaf" x="775" y="249" font-size="9.5">Ingredients</text>
    <g class="body on-accent" font-size="5.3">
      <text x="775" y="258">We use only the finest hand picked</text>
      <text x="775" y="265">ceylon green tea and mix it with</text>
      <text x="775" y="272">natural fruit pieces, a hint of natural</text>
      <text x="775" y="279">flavouring as our base. We add the</text>
      <text x="775" y="286">goodness of burdock root and</text>
      <text x="775" y="293">echinacea to help build your body's</text>
      <text x="775" y="300">defenses and sweeten it with a</text>
      <text x="775" y="307">dash of the south american stevia</text>
      <text x="775" y="314">leaf to give a great tasting drink</text>
      <text x="775" y="321">that will do you some good!</text>
    </g>

    <rect class="panel-leaf" x="529" y="346" width="237" height="134"/>
    <path class="flap-leaf" d="M529 480 L766 480 L766 495 Q766 503 756 503 L539 503 Q529 503 529 495 Z"/>
  </g>

  <!-- Zest box -->
  <g class="box-zest" transform="translate(6 524)">
    <path class="cut" d="M529 66 L518 66 L514 30 L500 20 L486 50 L486 140 L500 180 L529 195 Z"/>
    <path class="cut" d="M766 66 L777 66 L781 30 L795 20 L810 50 L810 140 L795 180 L766 195 Z"/>
    <path class="cut" d="M400 195 L405 170 L520 170 L529 195 Z"/>
    <path class="cut" d="M178 195 L186 177 L380 177 L390 195 Z"/>
    <path class="cut" d="M766 195 L775 168 L880 168 L891 195 Z"/>
    <path class="cut" d="M400 346 L405 370 L520 370 L529 346 Z"/>
    <path class="cut" d="M766 346 L775 372 L880 372 L891 346 Z"/>
    <path class="cut" d="M178 202 L137 210 L137 340 L178 346 Z"/>

    <rect class="panel-accent" x="529" y="18" width="237" height="48"/>
    <rect class="panel-white" x="529" y="66" width="237" height="129"/>
    <g transform="rotate(180 647 128)">
      <circle class="wordmark-dot" cx="610" cy="128" r="13"/>
      <text class="wordmark" x="630" y="137" font-size="25">Zest</text>
      <rect class="fruit-art" role="img" aria-label="Raspberry and pomegranate illustration" x="712" y="110" width="50" height="32" rx="16"/>
    </g>

    <rect class="panel-white" x="178" y="195" width="222" height="151"/>
    <circle class="wordmark-dot" cx="212" cy="236" r="12"/>
    <text class="wordmark" x="230" y="244" font-size="22">Zest</text>
    <rect class="fruit-art" role="img" aria-label="Raspberry and pomegranate illustration" x="312" y="218" width="50" height="30" rx="15"/>
    <text class="heading t-leaf" x="278" y="285" font-size="10" text-anchor="middle">5 reasons to drink this!!</text>
    <g class="body t-accent" font-size="5.6">
      <text x="218" y="299"><tspan class="t-leaf">+ </tspan>100% natural ingredients</text>
      <text x="218" y="307"><tspan class="t-leaf">+ </tspan>x% of your RDA of x</text>
      <text x="218" y="315"><tspan class="t-leaf">+ </tspan>x mg of antioxidants to keep your heart healthy.</text>
      <text x="218" y="323"><tspan class="t-leaf">+ </tspan>Naturally sweet taste</text>
      <text x="218" y="331"><tspan class="t-leaf">+ </tspan>only x calories per cup!</text>
    </g>

    <rect class="panel-accent" x="400" y="195" width="129" height="151"/>
    <text class="heading t-leaf" x="410" y="234" font-size="9.5">Nutrition Facts</text>
    <g class="body on-accent" font-size="5.2">
      <text x="410" y="242">Serving size: 1 tea bag (4g)</text>
      <text x="410" y="249">Makes: 8 fl. oz.</text>
      <text x="410" y="256">Servings per Container: 25</text>
    </g>
    <rect class="facts-box" x="405" y="262" width="114" height="58"/>
    <g class="body on-accent" font-size="5">
      <text x="409" y="270" font-size="6">Amount Per Serving</text>
      <text x="409" y="278">Calories</text><text x="445" y="278">0</text><text x="468" y="278">% Daily Value*</text>
      <text x="409" y="285">Total Fat</text><text x="445" y="285">0g</text><text x="468" y="285">0%</text>
      <text x="409" y="292">Sodium</text><text x="445" y="292">0mg</text><text x="468" y="292">5%</text>
      <text x="409" y="299">Total Carb.</text><text x="445" y="299">0g</text><text x="468" y="299">0%</text>
      <text x="409" y="306">Sugars</text><text x="445" y="306">10g</text>
      <text x="409" y="313">Protein</text><text x="445" y="313">0g</text>
      <text x="409" y="330">Percent Daily Values are based</text>
      <text x="409" y="337">on a 2,000 calorie diet</text>
    </g>

    <rect class="panel-white" x="529" y="195" width="237" height="151"/>
    <circle class="wordmark-dot" cx="608" cy="226" r="14"/>
    <text class="wordmark" x="629" y="236" font-size="27">Zest</text>
    <text class="body t-accent" x="665" y="246" font-size="5" text-anchor="middle">Green tea with vitamins drink</text>
    <rect class="fruit-art" role="img" aria-label="Raspberry and pomegranate illustration" x="622" y="262" width="54" height="40" rx="20"/>
    <text class="heading t-leaf" x="647" y="316" font-size="8.5" text-anchor="middle">rasberry &amp; pomegranate flavour</text>
    <g class="body t-accent" font-size="4.8" text-anchor="middle">
      <text x="647" y="324">Natural Ceylon green tea with added vitamins and herbs to</text>
      <text x="647" y="330">give you the best start to your day</text>
    </g>

    <rect class="panel-accent" x="766" y="195" width="125" height="151"/>
    <text class="heading t-leaf" x="775" y="251" font-size="9.5">Ingredients</text>
    <g class="body on-accent" font-size="5.3">
      <text x="775" y="260">We use only the finest hand picked</text>
      <text x="775" y="267">ceylon green tea and mix it with</text>
      <text x="775" y="274">natural fruit pieces, a hint of natural</text>
      <text x="775" y="281">flavouring as our base. We add the</text>
      <text x="775" y="288">goodness of burdock root and</text>
      <text x="775" y="295">echinacea to help build your body's</text>
      <text x="775" y="302">defenses and sweeten it with a</text>
      <text x="775" y="309">dash of the south american stevia</text>
      <text x="775" y="316">leaf to give a great tasting drink</text>
      <text x="775" y="323">that will do you some good!</text>
    </g>

    <rect class="panel-leaf" x="529" y="346" width="237" height="134"/>
    <path class="flap-leaf" d="M529 480 L766 480 L766 495 Q766 503 756 503 L539 503 Q529 503 529 495 Z"/>
  </g>
</svg>
</body>
</html>
```